Design logo and business card.

Design and construct logo and card for my business which is an over seeing company of other smaller businesses. The companies name is ember4 business works. Im open to any ideas but i am looking for a very cool contemporary design with a very prestige feel. The card can be either single or double sided, Thank you and i will look forward to your submissions.

Business

• Company name, email, website, telephone, my name. Cool modern look with a prestige feel.

```html
<!DOCTYPE html>
<html lang="en">
<head>
<meta charset="utf-8">
<title>ember4 business works – business card options</title>
<link rel="stylesheet" href="https://fonts.googleapis.com/css2?family=Open+Sans:wght@400;600&family=Archivo:wght@800&display=swap">
<style>
  :root {
    --page-bg: #ffffff;
    --card-pattern: #2c2a28;
    --card-base: #232120;
    --text-light: #ffffff;
    --label-ink: #1e1e1e;
    --accent-orange: #d9792a;
    --accent-purple: #8f5fa8;
  }
  html, body {
    margin: 0;
    padding: 0;
    overflow: hidden;
  }
  body {
    width: 1200px;
    height: 1000px;
    position: relative;
    background: var(--page-bg);
    font-family: "Open Sans", Arial, sans-serif;
  }
  .option-number {
    position: absolute;
    font-family: "Archivo", Arial, sans-serif;
    font-weight: 800;
    font-size: 62px;
    line-height: 1;
    color: var(--label-ink);
  }
  .accent-orange { --accent: var(--accent-orange); }
  .accent-purple { --accent: var(--accent-purple); }

  .card {
    position: absolute;
    width: 374px;
    height: 215px;
    border-radius: 16px;
    overflow: hidden;
    background: var(--card-base);
  }
  .card-pattern {
    position: absolute;
    left: 0; top: 0;
    width: 100%;
    background: var(--card-pattern);
  }
  .card-front .card-pattern { height: 100%; }
  .card-back .card-pattern { height: 115px; }

  .brand-name {
    position: absolute;
    left: 0; right: 0;
    top: 86px;
    text-align: center;
    font-weight: 400;
    font-size: 25px;
    letter-spacing: 0.5px;
    color: var(--accent);
  }
  .front-stripe {
    position: absolute;
    left: 0; top: 184px;
  }
  .web-address {
    position: absolute;
    left: 228px;
    top: 181px;
    width: 102px;
    text-align: center;
    font-size: 11px;
    color: var(--text-light);
  }

  .company-title {
    position: absolute;
    left: 0; right: 0;
    top: 74px;
    text-align: center;
    font-size: 19px;
    color: var(--text-light);
  }
  .back-rule {
    position: absolute;
    left: 0; right: 0;
    top: 113px;
    height: 5px;
    background: var(--accent);
  }
  .contact {
    position: absolute;
    left: 0; right: 0;
    top: 134px;
    text-align: center;
    color: var(--text-light);
  }
  .contact-name {
    margin: 0 0 4px;
    font-size: 15px;
    color: var(--accent);
  }
  .contact-line {
    margin: 0;
    font-size: 10.5px;
    font-weight: 600;
    line-height: 17px;
  }
  .contact-line svg {
    vertical-align: -1px;
    margin-right: 3px;
  }
</style>
</head>
<body>

  <div class="option-number" style="left:88px; top:86px;">1</div>
  <div class="option-number" style="left:1075px; top:72px;">2</div>
  <div class="option-number" style="left:58px; top:733px;">3</div>
  <div class="option-number" style="left:1077px; top:711px;">4</div>

  <!-- Option 1 -->
  <section class="accent-orange">
    <div class="card card-front" style="left:213px; top:2px;">
      <div class="card-pattern" role="img" aria-label="Dark damask pattern background"></div>
      <div class="brand-name">ember4 business works</div>
      <svg class="front-stripe" width="374" height="8" viewBox="0 0 374 8">
        <polygon points="0,0 228,0 225,8 0,8" fill="var(--accent)"/>
        <polygon points="341,0 374,0 374,8 338,8" fill="var(--accent)"/>
      </svg>
      <div class="web-address">www. ember-4.com</div>
    </div>
    <div class="card card-back" style="left:210px; top:255px;">
      <div class="card-pattern" role="img" aria-label="Dark damask pattern background"></div>
      <div class="company-title">EMBER4 BUSINESS WORKS</div>
      <div class="back-rule"></div>
      <div class="contact">
        <p class="contact-name">RAFA LORNE</p>
        <p class="contact-line"><svg width="6" height="9" viewBox="0 0 6 9"><rect x="0.5" y="0.5" width="5" height="8" rx="1" fill="none" stroke="currentColor"/></svg>+34 600 555 019</p>
        <p class="contact-line"><svg width="9" height="7" viewBox="0 0 9 7"><rect x="0.5" y="0.5" width="8" height="6" fill="none" stroke="currentColor"/><polyline points="0.5,0.5 4.5,4 8.5,0.5" fill="none" stroke="currentColor"/></svg>info@ember-4.com</p>
      </div>
    </div>
  </section>

  <!-- Option 2 -->
  <section class="accent-orange">
    <div class="card card-front" style="left:620px; top:2px;">
      <div class="card-pattern" role="img" aria-label="Dark damask pattern background"></div>
      <div class="brand-name">ember4 business works</div>
      <svg class="front-stripe" width="374" height="8" viewBox="0 0 374 8">
        <polygon points="0,0 220,0 217,8 0,8" fill="var(--accent)"/>
        <polygon points="341,0 374,0 374,8 338,8" fill="var(--accent)"/>
      </svg>
      <div class="web-address">www. ember-4.com</div>
    </div>
    <div class="card card-back" style="left:618px; top:255px;">
      <div class="card-pattern" role="img" aria-label="Dark damask pattern background"></div>
      <div class="company-title">EMBER4 BUSINESS WORKS</div>
      <div class="back-rule"></div>
      <div class="contact">
        <p class="contact-name">RAFA LORNE</p>
        <p class="contact-line"><svg width="6" height="9" viewBox="0 0 6 9"><rect x="0.5" y="0.5" width="5" height="8" rx="1" fill="none" stroke="currentColor"/></svg>+34 600 555 019</p>
        <p class="contact-line"><svg width="9" height="7" viewBox="0 0 9 7"><rect x="0.5" y="0.5" width="8" height="6" fill="none" stroke="currentColor"/><polyline points="0.5,0.5 4.5,4 8.5,0.5" fill="none" stroke="currentColor"/></svg>info@ember-4.com</p>
      </div>
    </div>
  </section>

  <!-- Option 3 -->
  <section class="accent-purple">
    <div class="card card-front" style="left:213px; top:528px;">
      <div class="card-pattern" role="img" aria-label="Dark damask pattern background"></div>
      <div class="brand-name">ember4 business works</div>
      <svg class="front-stripe" width="374" height="8" viewBox="0 0 374 8">
        <polygon points="0,0 228,0 225,8 0,8" fill="var(--accent)"/>
        <polygon points="341,0 374,0 374,8 338,8" fill="var(--accent)"/>
      </svg>
      <div class="web-address">www. ember-4.com</div>
    </div>
    <div class="card card-back" style="left:210px; top:781px;">
      <div class="card-pattern" role="img" aria-label="Dark damask pattern background"></div>
      <div class="company-title">EMBER4 BUSINESS WORKS</div>
      <div class="back-rule"></div>
      <div class="contact">
        <p class="contact-name">RAFA LORNE</p>
        <p class="contact-line"><svg width="6" height="9" viewBox="0 0 6 9"><rect x="0.5" y="0.5" width="5" height="8" rx="1" fill="none" stroke="currentColor"/></svg>+34 600 555 019</p>
        <p class="contact-line"><svg width="9" height="7" viewBox="0 0 9 7"><rect x="0.5" y="0.5" width="8" height="6" fill="none" stroke="currentColor"/><polyline points="0.5,0.5 4.5,4 8.5,0.5" fill="none" stroke="currentColor"/></svg>info@ember-4.com</p>
      </div>
    </div>
  </section>

  <!-- Option 4 -->
  <section class="accent-purple">
    <div class="card card-front" style="left:620px; top:528px;">
      <div class="card-pattern" role="img" aria-label="Dark damask pattern background"></div>
      <div class="brand-name">ember4 business works</div>
      <svg class="front-stripe" width="374" height="8" viewBox="0 0 374 8">
        <polygon points="0,0 220,0 217,8 0,8" fill="var(--accent)"/>
        <polygon points="341,0 374,0 374,8 338,8" fill="var(--accent)"/>
      </svg>
      <div class="web-address">www. ember-4.com</div>
    </div>
    <div class="card card-back" style="left:618px; top:781px;">
      <div class="card-pattern" role="img" aria-label="Dark damask pattern background"></div>
      <div class="company-title">EMBER4 BUSINESS WORKS</div>
      <div class="back-rule"></div>
      <div class="contact">
        <p class="contact-name">RAFA LORNE</p>
        <p class="contact-line"><svg width="6" height="9" viewBox="0 0 6 9"><rect x="0.5" y="0.5" width="5" height="8" rx="1" fill="none" stroke="currentColor"/></svg>+34 600 555 019</p>
        <p class="contact-line"><svg width="9" height="7" viewBox="0 0 9 7"><rect x="0.5" y="0.5" width="8" height="6" fill="none" stroke="currentColor"/><polyline points="0.5,0.5 4.5,4 8.5,0.5" fill="none" stroke="currentColor"/></svg>info@ember-4.com</p>
      </div>
    </div>
  </section>

</body>
</html>
```